WordPress webdesign with coding for our company BRISK The Answer

BRISK The Answer is a payrolling company such as Montaval Wages (one of our competitor https://www.montaval-wages.ch/fr/). We need to set up our website in both languages (Fr and Eng). Our logo is enclosed.
we would like something simple explaining what is payrolling in Graph and wording, who we are and a contact page. you can also take some example if needed from our mother company BRISK The Horizon (www.briskthehorizon.ch) or our sister company (www.briskyourstride.ch). we would like to keep the color panel of our logo (ref. Black = PANTONE P Process Black C
Pink = PANTONE P Process Magenta C
Grey = PANTONE 430 C) as the driver of the website.

```html
<!DOCTYPE html>
<html lang="en">
<head>
<meta charset="utf-8">
<title>BRISK The Answer – Payrolling</title>
<link href="https://fonts.googleapis.com/css2?family=Inter:wght@400;500;600;700&display=swap" rel="stylesheet">
<style>
:root{
  --pink:#e8318f;
  --pink-soft:#fbd3e6;
  --ink:#1f1c1d;
  --grey:#7c878e;
  --grey-light:#b5bcc0;
  --line:#ececec;
  --bg-soft:#f4f4f4;
  --footer:#231f20;
  --white:#ffffff;
}
*{box-sizing:border-box;margin:0;padding:0}
html,body{width:1200px;height:4096px;overflow:hidden}
body{font-family:"Inter",sans-serif;color:var(--ink);background:var(--white);position:relative}
.abs{position:absolute}
.pink{color:var(--pink)}
.btn{position:absolute;display:flex;align-items:center;justify-content:center;background:var(--pink);color:var(--white);font-weight:700;font-size:14px;letter-spacing:.3px;border-radius:30px;text-transform:uppercase}
.btn-outline{background:transparent;border:2px solid var(--white)}
.h2{font-weight:700;font-size:32px;line-height:1.4}
.body-text{font-size:13px;line-height:24px;color:var(--grey)}

/* header */
.site-header{position:absolute;top:0;left:0;width:1200px;height:86px;background:var(--white)}
.brand{position:absolute;display:flex;align-items:center;gap:10px;font-weight:700;font-size:26px;color:var(--ink)}
.brand-mark{width:16px;height:16px;background:var(--pink)}
.main-nav{position:absolute;left:414px;top:34px;display:flex;gap:39px;font-size:14px;font-weight:500}
.main-nav .active{color:var(--pink)}
.lang{position:absolute;left:994px;top:34px;font-size:14px;font-weight:500;display:flex;align-items:center;gap:6px}
.lang-dot{width:14px;height:14px;border-radius:50%;background:#c9d3e6}

/* hero */
.hero{position:absolute;top:86px;left:0;width:1200px;height:571px;background:linear-gradient(90deg,#f1f2f3 0%,#e3e5e6 40%,#9aa3aa 70%,#4b5a6b 100%)}
.hero h1{position:absolute;left:144px;top:96px;font-size:46px;line-height:63px;font-weight:700}
.hero-rule{position:absolute;left:0;top:246px;width:395px;height:4px;background:var(--pink)}
.hero-rule-dots{position:absolute;left:402px;top:246px;width:18px;height:4px;background:radial-gradient(circle,var(--pink) 2px,transparent 2.5px) 0 0/9px 4px}
.hero p{position:absolute;left:144px;top:269px;width:440px;font-size:17px;line-height:29px;color:var(--ink)}
.hero-visual{position:absolute;left:560px;top:0;width:640px;height:571px}

/* services */
.services{position:absolute;top:657px;left:0;width:1200px;height:707px}
.svc-photo{position:absolute;left:165px;top:48px;width:420px;height:570px;border-radius:6px;background:linear-gradient(180deg,#ece7e4,#d9d2cf)}
.svc-frame{position:absolute;left:86px;top:110px;width:494px;height:540px;border:2px dashed var(--pink);border-radius:10px;transform:rotate(-3deg)}
.svc-pinkblock{position:absolute;left:440px;top:350px;width:120px;height:250px;background:var(--pink-soft);border-radius:8px}
.badge-credit{position:absolute;left:125px;top:196px;width:144px;height:66px;background:var(--white);border-radius:6px;box-shadow:0 6px 20px rgba(0,0,0,.12);padding:13px 15px}
.badge-credit b{font-size:20px;color:var(--pink);font-weight:600}
.badge-credit span{display:block;font-size:10px;color:var(--ink)}
.badge-price{position:absolute;left:49px;top:389px;width:114px;height:46px;background:var(--pink);color:var(--white);border-radius:5px;font-size:20px;font-weight:600;display:flex;align-items:center;justify-content:center}
.badge-price small{font-size:10px;font-style:italic;margin-left:2px;margin-top:6px}
.svc-title{position:absolute;left:678px;top:100px;font-size:31px;font-weight:700}
.svc-track{position:absolute;left:643px;top:222px;width:2px;height:160px;background:linear-gradient(var(--pink),transparent)}
.svc-knob{position:absolute;left:636px;top:222px;width:16px;height:16px;border-radius:50%;background:var(--pink);border:3px solid #f9c6de}
.svc-item{position:absolute;left:680px;width:375px;height:126px;padding:22px 20px 0 86px}
.svc-item h3{font-size:17px;font-weight:500;margin-bottom:10px}
.svc-item p{font-size:13px;line-height:23px}
.svc-item svg{position:absolute;left:20px;top:26px}
.svc-item.is-active{background:var(--pink);color:var(--white);border-radius:4px;box-shadow:0 8px 20px rgba(232,49,143,.3)}
.svc-item.muted{color:var(--grey)}
.svc-item.faint{color:var(--grey-light)}
.svc-divider{position:absolute;left:680px;width:375px;height:1px;background:var(--line)}

/* about */
.about{position:absolute;top:1364px;left:0;width:1200px;height:459px;background:var(--bg-soft)}
.about-photo{position:absolute;left:590px;top:0;width:610px;height:459px;background:linear-gradient(90deg,var(--bg-soft) 0%,#e8e9e9 20%,#cbb69a 70%,#b57a2f 100%)}
.about h2{position:absolute;left:143px;top:44px}
.about .body-text{position:absolute;left:143px;width:436px;text-align:justify}

/* why */
.why{position:absolute;top:1823px;left:0;width:1200px;height:460px;background:var(--pink)}
.why h2{position:absolute;left:0;top:62px;width:1200px;text-align:center;color:var(--white);font-size:31px;font-weight:600}
.why-card{position:absolute;top:146px;width:295px;height:243px;background:var(--white);border-radius:6px;text-align:center;padding-top:26px}
.why-card h3{font-size:18px;font-weight:500;margin:14px 0 10px}
.why-card p{font-size:13px;line-height:24px;color:var(--grey);padding:0 30px}

/* what is */
.what{position:absolute;top:2283px;left:0;width:1200px;height:499px}
.what h2{position:absolute;left:143px;top:88px}
.what .body-text{position:absolute;left:143px;width:445px}
.what-graphic{position:absolute;left:652px;top:76px;width:405px;height:388px;border-radius:50%;background:radial-gradient(circle,#fdf0e3 0%,#f3f4f6 55%,#ffffff 72%)}

/* partner */
.partner{position:absolute;top:2782px;left:0;width:1200px;height:572px}
.partner h2{position:absolute;left:0;top:30px;width:1200px;text-align:center;font-size:31px;font-weight:600}
.partner-card-back{position:absolute;left:160px;top:150px;width:880px;height:370px;border-radius:22px;background:var(--white);box-shadow:0 4px 16px rgba(0,0,0,.06)}
.partner-card{position:absolute;left:145px;top:116px;width:910px;height:377px;border-radius:22px;background:var(--white);box-shadow:0 8px 30px rgba(0,0,0,.1)}
.partner-card h3{position:absolute;left:40px;top:140px;font-size:19px;font-weight:500}
.partner-card .lead{position:absolute;left:40px;top:180px;width:360px;font-size:16px;line-height:28px;color:#444}
.partner-list{position:absolute;left:40px;top:260px;list-style:none;font-size:13px;color:var(--grey)}
.partner-list li{display:flex;align-items:center;gap:14px;height:27px}
.tick{width:12px;height:12px;border-radius:50%;background:var(--pink);display:inline-block;position:relative}
.tick::after{content:"";position:absolute;left:3px;top:2px;width:4px;height:6px;border:solid var(--white);border-width:0 2px 2px 0;transform:rotate(40deg)}
.partner-photo{position:absolute;left:455px;top:40px;width:410px;height:298px;border-radius:14px;background:linear-gradient(135deg,#3b3a3f 0%,#9a9aa1 50%,#efeff2 100%)}
.arrow-btn{position:absolute;width:36px;height:36px;border-radius:50%;display:flex;align-items:center;justify-content:center}

/* testimonials */
.testimonials{position:absolute;top:3354px;left:0;width:1200px;height:410px}
.testimonials h2{position:absolute;left:143px;top:40px;font-size:31px;font-weight:600}
.testi-card{position:absolute;top:112px;width:294px;height:184px;background:var(--white);box-shadow:0 4px 18px rgba(0,0,0,.06);padding:26px 24px}
.stars{color:#f5a623;font-size:17px;letter-spacing:4px}
.testi-card p{font-size:13px;line-height:24px;color:#555;margin:10px 0 18px}
.testi-card b{font-weight:500;font-size:15px}
.testi-card.fade{opacity:.35}
.dots{position:absolute;top:324px;left:578px;display:flex;gap:9px}
.dots i{width:10px;height:10px;border-radius:50%;border:1.5px solid var(--ink);display:block}
.dots i.on{background:var(--pink);border-color:var(--pink)}

/* footer */
.site-footer{position:absolute;top:3764px;left:0;width:1200px;height:332px;background:var(--footer);color:var(--white)}
.footer-col{position:absolute;top:140px;font-size:13px;line-height:24px}
.footer-col h4{font-size:15px;font-weight:500;margin-bottom:4px}
.contact-row{display:flex;gap:10px}
.contact-row svg{margin-top:6px}
.social li{list-style:none;display:flex;align-items:center;gap:14px}
.social i{width:8px;height:8px;background:var(--white);display:inline-block}
.footer-rule{position:absolute;left:143px;top:275px;width:912px;height:1px;background:#555}
.copyright{position:absolute;top:295px;width:1200px;text-align:center;font-size:13px}
</style>
</head>
<body>

<header class="site-header">
  <div class="brand" style="left:144px;top:27px"><span>BRISK The Answer</span><span class="brand-mark"></span></div>
  <nav class="main-nav">
    <span class="active">HOME</span><span>ABOUT</span><span>BUSINESS</span><span>CONSULTANT</span><span>AGENCY</span><span>BLOG</span>
  </nav>
  <div class="lang"><span class="lang-dot"></span>EN ▾</div>
</header>

<section class="hero">
  <div class="hero-visual" role="img" aria-label="Photo of a man in glasses reviewing payroll documents at a laptop"></div>
  <h1>We <span class="pink">Handle</span> Payroll,<br>You Handle <span class="pink">Growth.</span></h1>
  <div class="hero-rule"></div><div class="hero-rule-dots"></div>
  <p>Lorem ipsum dolor sit amet, consectetur adipiscing elit, sed do eiusmod tempor incididunt.</p>
  <a class="btn" style="left:143px;top:362px;width:248px;height:52px">Discover Payrolling</a>
</section>

<section class="services">
  <div class="svc-frame"></div>
  <div class="svc-pinkblock"></div>
  <div class="svc-photo" role="img" aria-label="Photo of a smiling woman holding a smartphone"></div>
  <div class="badge-credit"><b>▲ $40,000</b><span>Salary Credited</span></div>
  <div class="badge-price">$799<small>/Mon</small></div>

  <h2 class="svc-title"><span class="pink" style="font-weight:500">Discover All</span> Our Services</h2>
  <div class="svc-track"></div><div class="svc-knob"></div>

  <div class="svc-item is-active" style="top:168px">
    <svg width="50" height="54" viewBox="0 0 50 54" fill="none" stroke="#fff" stroke-width="2"><circle cx="25" cy="27" r="22"/><circle cx="25" cy="27" r="11"/><path d="M25 20v14M21 24h6a2 2 0 010 4h-4a2 2 0 000 4h6"/></svg>
    <h3>Payrolling</h3>
    <p>Lorem ipsum dolor consectetur adipiscing elit, sed do eiusmod tempor incididunt.</p>
  </div>
  <div class="svc-item muted" style="top:294px">
    <svg width="56" height="56" viewBox="0 0 56 56" fill="none" stroke="#555" stroke-width="2"><circle cx="28" cy="28" r="12"/><rect x="2" y="2" width="12" height="12"/><rect x="42" y="2" width="12" height="12"/><rect x="2" y="42" width="12" height="12"/><rect x="42" y="42" width="12" height="12"/><path d="M14 14l6 6M42 14l-6 6M14 42l6-6M42 42l-6-6"/></svg>
    <h3>Sourcing</h3>
    <p>Lorem ipsum dolor consectetur adipiscing elit, sed do eiusmod tempor incididunt.</p>
  </div>
  <div class="svc-divider" style="top:418px"></div>
  <div class="svc-item faint" style="top:420px">
    <svg width="46" height="60" viewBox="0 0 46 60" fill="none" stroke="#ccc" stroke-width="2"><rect x="4" y="4" width="32" height="52" rx="3"/><path d="M12 40h16M12 46h10M28 16l4 4 10-10"/></svg>
    <h3>Payroll Outsourcing</h3>
    <p>Lorem ipsum dolor consectetur adipiscing elit, sed do eiusmod tempor incididunt.</p>
  </div>
  <a class="btn" style="left:680px;top:560px;width:152px;height:48px">Contact Us</a>
</section>

<section class="about">
  <div class="about-photo" role="img" aria-label="Photo of a smiling man working on a laptop in a bright office"></div>
  <h2 class="h2"><span class="pink" style="font-weight:500">BRISK The Answer</span> Payroll,<br>Swiss leader in Payrolling</h2>
  <p class="body-text" style="top:154px">Lorem ipsum dolor sit amet, consectetur adipiscing elit, sed do eiusmod tempor incididunt ut labore et dolore magna aliqua. Ut enim ad minim veniam, quis nostrud exercitation ullamco laboris nisi ut aliquip ex ea commodo consequat.</p>
  <p class="body-text" style="top:264px">Duis aute irure dolor in reprehenderit in voluptate velit esse cillum dolore eu fugiat nulla pariatur. Excepteur sint occaecat cupidatat non proident, sunt in culpa qui officia deserunt.</p>
  <a class="btn" style="left:143px;top:359px;width:216px;height:46px">Discover Payrolling</a>
</section>

<section class="why">
  <h2>Why Choose BRISK The Answer?</h2>
  <div class="why-card" style="left:145px">
    <svg width="70" height="64" viewBox="0 0 70 64" fill="none" stroke="#e8318f" stroke-width="2"><circle cx="35" cy="22" r="9"/><path d="M20 58c0-10 7-18 15-18s15 8 15 18z"/><circle cx="35" cy="26" r="22" stroke-dasharray="4 4"/></svg>
    <h3>Management</h3>
    <p>Nemo enim ipsam voluptatem quia voluptas sit aspernatur aut odit aut fugit, sed quia consequuntur</p>
  </div>
  <div class="why-card" style="left:453px">
    <svg width="70" height="64" viewBox="0 0 70 64" fill="none" stroke="#e8318f" stroke-width="2"><rect x="14" y="4" width="36" height="54" rx="2"/><path d="M20 16l3 3 5-5M32 16h12M20 30l3 3 5-5M32 30h12M20 44l3 3 5-5M32 44h12"/></svg>
    <h3>Expertise</h3>
    <p>Nemo enim ipsam voluptatem quia voluptas sit aspernatur aut odit aut fugit, sed quia consequuntur</p>
  </div>
  <div class="why-card" style="left:760px">
    <svg width="70" height="64" viewBox="0 0 70 64" fill="none" stroke="#e8318f" stroke-width="2"><rect x="20" y="6" width="22" height="12" rx="2" transform="rotate(35 31 12)"/><path d="M28 22L14 44"/><rect x="34" y="50" width="28" height="8"/></svg>
    <h3>Accompaniement</h3>
    <p>Nemo enim ipsam voluptatem quia voluptas sit aspernatur aut odit aut fugit, sed quia consequuntur</p>
  </div>
</section>

<section class="what">
  <h2 class="h2">What is <span class="pink" style="font-weight:500">Payrolling?</span></h2>
  <p class="body-text" style="top:154px">Lorem ipsum dolor sit amet, consectetur adipiscin sed do eiusmod tempor incididunt ut labore et dolore magna aliqua. Ut enim ad minim veniam, quis nostrud exercitation ullamco laboris nisi ut aliquip ex ea commodo consequat. Duis aute irure dolor reprehenderit in voluptate velit esse cillum dolore eu fugiat nulla pariatur.</p>
  <p class="body-text" style="top:282px">Sed ut perspiciatis unde omnis iste natus error sit voluptatem accusantium doloremque laudantium, totam rem aperiam, eaque ipsa quae ab illo inventore veritatis et quasi architecto beatae vitae dicta sunt explicabo. Nemo enim ipsam voluptatem quia.</p>
  <a class="btn" style="left:143px;top:395px;width:217px;height:46px">Discover Payrolling</a>
  <div class="what-graphic" role="img" aria-label="Illustration of a finance cycle with coins, bar chart, savings and money bag around a dashed circle"></div>
</section>

<section class="partner">
  <h2>Working With <span class="pink" style="font-weight:500">Brisk Payroll</span> Means <span class="pink" style="font-weight:500">Working</span> With A Partner</h2>
  <div class="partner-card-back"></div>
  <div class="partner-card">
    <svg class="abs" style="left:40px;top:54px" width="66" height="64" viewBox="0 0 66 64" fill="none" stroke="#e8318f" stroke-width="2"><circle cx="33" cy="18" r="8"/><circle cx="33" cy="18" r="14" stroke-dasharray="5 3"/><circle cx="14" cy="40" r="5"/><circle cx="33" cy="40" r="5"/><circle cx="52" cy="40" r="5"/><path d="M6 60v-8h16v8M25 60v-8h16v8M44 60v-8h16v8"/></svg>
    <h3>MARKET LEADER</h3>
    <p class="lead">Lorem ipsum dolor sit amet, consectetur adipiscing elit, sed do eiusmod</p>
    <ul class="partner-list">
      <li><span class="tick"></span>Lorem ipsum dolor sit amet, consectetur adipiscing</li>
      <li><span class="tick"></span>Sed do eiusmod tempor incididunt ut labore et</li>
      <li><span class="tick"></span>Dolore magna aliqua ut enim ad minim</li>
    </ul>
    <div class="partner-photo" role="img" aria-label="Photo of a woman reading a document beside a payroll concept sketch"></div>
  </div>
  <div class="arrow-btn" style="left:79px;top:2978px;top:296px;background:var(--white);box-shadow:0 2px 8px rgba(0,0,0,.15)"><svg width="10" height="14" viewBox="0 0 10 14" fill="none" stroke="#1f1c1d" stroke-width="2"><path d="M8 1L2 7l6 6"/></svg></div>
  <div class="arrow-btn" style="left:1084px;top:296px;background:var(--pink)"><svg width="10" height="14" viewBox="0 0 10 14" fill="none" stroke="#fff" stroke-width="2"><path d="M2 1l6 6-6 6"/></svg></div>
</section>

<section class="testimonials">
  <h2><span class="pink" style="font-weight:500">Client</span> Testimonials</h2>
  <a class="btn" style="left:836px;top:35px;width:216px;height:46px">Discover Payrolling</a>
  <div class="testi-card fade" style="left:-165px"><div class="stars">★★★★★</div><p>Lorem ipsum dolor sit amet, consectetur adipiscing elit, sed do eiusmod tempor incididunt ut labore et dolore</p><b>- Anna V</b></div>
  <div class="testi-card" style="left:143px"><div class="stars">★★★★★</div><p>Lorem ipsum dolor sit amet, consectetur adipiscing elit, sed do eiusmod tempor incididunt ut labore et dolore</p><b>- Laura P.</b></div>
  <div class="testi-card" style="left:452px"><div class="stars">★★★★★</div><p>Lorem ipsum dolor sit amet, consectetur adipiscing elit, sed do eiusmod tempor incididunt ut labore et dolore</p><b>- Marc D.</b></div>
  <div class="testi-card" style="left:760px"><div class="stars">★★★★★</div><p>Lorem ipsum dolor sit amet, consectetur adipiscing elit, sed do eiusmod tempor incididunt ut labore et dolore</p><b>- S Keller</b></div>
  <div class="testi-card fade" style="left:1069px"><div class="stars">★★★★★</div><p>Lorem ipsum dolor sit amet, consectetur adipiscing elit, sed do eiusmod tempor incididunt ut labore et dolore</p><b>- Anna V</b></div>
  <div class="dots"><i class="on"></i><i></i><i></i></div>
</section>

<footer class="site-footer">
  <div class="brand" style="left:144px;top:58px;color:var(--white);font-size:30px"><span>BRISK The Answer</span><span class="brand-mark"></span></div>
  <a class="btn" style="left:678px;top:48px;width:150px;height:46px">Contact Us</a>
  <a class="btn btn-outline" style="left:840px;top:48px;width:215px;height:46px">Discover Payrolling</a>

  <div class="footer-col" style="left:143px">
    <div class="contact-row"><svg width="14" height="14" viewBox="0 0 14 14" fill="#e8318f"><path d="M3 1l3 3-2 2c1 2 2 3 4 4l2-2 3 3-2 3C6 13 1 8 1 3z"/></svg><div><h4>Phone</h4>+41 22 555 01 23</div></div>
    <div class="contact-row" style="margin-top:10px"><svg width="14" height="12" viewBox="0 0 14 12" fill="#e8318f"><rect width="14" height="12" rx="1"/><path d="M1 1l6 5 6-5" stroke="#231f20" fill="none"/></svg><div><h4>Email</h4>info@briskthehorizon.ch</div></div>
  </div>
  <div class="footer-col" style="left:405px"><h4>CONSULTANT</h4>How Payrolling Works<br>Our Payrolling Offer<br>Frequently Asked Questions</div>
  <div class="footer-col" style="left:653px"><h4>BUSINESS</h4>External talent management<br>Payroll Outsourcing<br>Talent sourcing</div>
  <div class="footer-col" style="left:931px"><h4>SOCIAL MEDIAS</h4>
    <ul class="social"><li><i></i>Community</li><li><i></i>Video Channel</li><li><i></i>Newsfeed</li></ul>
  </div>
  <div class="footer-rule"></div>
  <div class="copyright">© 2025 BRISK The Answer  -  All Rights Reserved</div>
</footer>

</body>
</html>
```